Buch-/eBook-Cover für Roman
Kelpwind hat stets schnell und kreativ auf Verbesserungsvorschläge reagiert - gerne wieder!
Zielgruppe
Ich bin Selfpublisher und möchte meinen vierten Roman veröffentlichen. Ich suche ein hochwertiges Cover, das im Buchhandel direkt ins Auge sticht.
Zielgruppe: junge Erwachsene/Erwachsene, Genre Thriller
Aufgabenstellung
Für meinen neuer Thriller „WAS DIE NACHT BEHÄLT“ suche ich ein aussagekräftiges Cover.
Es sollte den Inhalt des Buches widerspiegeln, den ich nachfolgend so gut es geht erläutere.
Klappentext:
Nur ein paar Minuten, dann würde er sich fortschleichen. Und bis dahin würde er die Augen zusammenkneifen, das Regenwetter ignorieren und gucken. Denn das hatte er schon immer geliebt. Gucken. Beobachten.
Alle Orte sehen, die er noch erleben wollte: Seitdem ihr Verlobter bei einem tragischen Unfall ums Leben kam, sind Lost Places mehr als nur eine Leidenschaft für Miriam. Sie sind alles, was ihr von ihrer gemeinsamen Zeit geblieben ist. Als Torben Kessrik, bekannter Urbexer und Schriftsteller, sie zu einer Gruppenreise auf das verwaiste Kreuzfahrtschiff Morvane Ostrika einlädt, scheint ein Traum in Erfüllung zu gehen. Fernab der Ufer Grönlands taucht Miriam nicht nur in die Geheimnisse des stählernen Riesen ein, sondern findet in Torben eine zweite Chance auf Liebe. Doch was zunächst wirkt wie das größte Abenteuer ihres Lebens, verwandelt sich rasch in eine Nacht des Grauens. Ihre Mitreisenden sind nicht, wer sie zu sein scheinen, und verborgen in den Schatten lauert etwas, das nur darauf wartet, dass die Jagd beginnt.
Weiterer Inhalt:
In der Geschichte kommt es zu blutigen Szenen, Kämpfen und Fluchtversuchen. Der Haupthandlungsort ist ein vergessenes Kreuzfahrtschiff, ein wahrer Lost Place auf hoher See, das vor der Küste Grönlands in arktischen Gewässern treibt. Kälte ist auf dem Schiff allgegenwärtig, sowie die Dunkelheit und absolute Stille. Das Cover sollte/könnte mehrere Inhalte dieses Schiffes abbilden, so zumindest meine Idee. Gerne lasse ich mich aber auch auf andere Vorschläge ein.
Wichtig ist, dass eine bedrohliche, unheimliche und spannende Atmosphäre erzeugt werden soll.
Das Schiff, grob beschrieben:
- Ein mittelgroßes Kreuzfahrtschiff, seit knapp zehn Jahren den Naturgewalte..

```html
<!DOCTYPE html>
<html lang="de">
<head>
<meta charset="utf-8">
<title>Was die Nacht behält – Malte Brünger</title>
<link rel="stylesheet" href="https://fonts.googleapis.com/css2?family=Cinzel:wght@400;500&family=Marcellus+SC&display=swap">
<style>
  :root {
    --page-bg: #ecebea;
    --cover-dark: #171312;
    --cover-mid: #2a2220;
    --cover-rust: #3b2420;
    --text-light: #efe9e4;
    --text-soft: #d8d0ca;
    --art-rust: #7a5034;
    --art-teal: #3f5a53;
    --art-shadow: #1b1513;
  }
  * { margin: 0; padding: 0; box-sizing: border-box; }
  html, body {
    width: 1200px; height: 959px; overflow: hidden;
    background: var(--page-bg);
  }
  .wrap {
    position: absolute; left: 145px; top: 150px;
    width: 910px; height: 660px;
    display: flex;
    box-shadow: 0 18px 40px rgba(0,0,0,.25);
  }
  .panel {
    position: relative; height: 100%;
    background:
      radial-gradient(ellipse at 30% 25%, rgba(90,40,30,.35), transparent 60%),
      radial-gradient(ellipse at 75% 70%, rgba(70,30,25,.4), transparent 55%),
      linear-gradient(160deg, var(--cover-mid), var(--cover-dark) 55%, var(--cover-rust));
    color: var(--text-light);
  }
  .back { width: 420px; padding: 70px 44px 0 44px; }
  .spine { width: 70px; border-left: 1px solid rgba(0,0,0,.5); border-right: 1px solid rgba(0,0,0,.5); }
  .front { width: 420px; overflow: hidden; }

  .title {
    font-family: "Cinzel", serif; font-weight: 400;
    line-height: 1; letter-spacing: .01em;
  }
  .back .title { font-size: 34px; }
  .back .title span { display: block; }
  .back .title .second { font-size: 25px; margin-top: 4px; }

  .blurb {
    font-family: "Marcellus SC", serif;
    font-size: 10.4px; line-height: 1.95;
    color: var(--text-soft);
    margin-top: 26px;
  }
  .blurb p + p { margin-top: 18px; }

  .spine-text {
    position: absolute; left: 50%; top: 50%;
    transform: translate(-50%, -50%) rotate(90deg);
    width: 620px;
    display: flex; justify-content: space-between; align-items: center;
    white-space: nowrap;
  }
  .spine-title { font-family: "Cinzel", serif; font-size: 31px; letter-spacing: .02em; }
  .spine-author { font-family: "Cinzel", serif; font-size: 14px; letter-spacing: .06em; }

  .front .title {
    position: absolute; left: 0; right: 0; top: 52px;
    text-align: center; font-size: 50px;
    z-index: 1;
  }
  .front .title span { display: block; }
  .front .title .second { font-size: 34px; margin-top: 6px; }

  .cover-art {
    position: absolute; left: 0; right: 0; top: 190px; bottom: 80px;
    background:
      radial-gradient(ellipse at 50% 65%, rgba(122,80,52,.75), transparent 65%),
      radial-gradient(ellipse at 75% 40%, rgba(63,90,83,.55), transparent 60%),
      linear-gradient(180deg, rgba(27,21,19,0), var(--art-shadow));
  }
  .front-author {
    position: absolute; left: 0; right: 0; bottom: 42px;
    text-align: center; font-family: "Cinzel", serif;
    font-size: 14px; letter-spacing: .06em;
  }
  .genre {
    position: absolute; left: 0; right: 0; bottom: 24px;
    text-align: center; font-family: "Cinzel", serif;
    font-size: 8.5px; letter-spacing: .12em; color: var(--text-soft);
  }
</style>
</head>
<body>
  <main class="wrap">
    <section class="panel back">
      <h2 class="title"><span>Was die</span><span class="second">Nacht behält</span></h2>
      <div class="blurb">
        <p>Nur ein paar Minuten, dann würde er sich fortschleichen. Und bis dahin würde er die Augen zusammenkneifen, das Regenwetter ignorieren und gucken. Denn das hatte er schon immer geliebt. Gucken. Beobachten.</p>
        <p>Alle Orte sehen, die er noch erleben wollte: Seitdem ihr Verlobter bei einem tragischen Unfall ums Leben kam, sind Lost Places mehr als nur eine Leidenschaft für Miriam. Sie sind alles, was ihr von ihrer gemeinsamen Zeit geblieben ist. Als Torben Kessrik, bekannter Urbexer und Schriftsteller, sie zu einer Gruppenreise auf das verwaiste Kreuzfahrtschiff Morvane Ostrika einlädt, scheint ein Traum in Erfüllung zu gehen. Fernab der Ufer Grönlands taucht Miriam nicht nur in die Geheimnisse des stählernen Riesen ein, sondern findet in Torben eine zweite Chance auf Liebe. Doch was zunächst wirkt wie das größte Abenteuer ihres Lebens, verwandelt sich rasch in eine Nacht des Grauens. Ihre Mitreisenden sind nicht, wer sie zu sein scheinen, und verborgen in den Schatten lauert etwas, das nur darauf wartet, dass die Jagd beginnt.</p>
      </div>
    </section>

    <section class="panel spine">
      <div class="spine-text">
        <span class="spine-title">WAS DIE NACHT BEHÄLT</span>
        <span class="spine-author">MALTE BRÜNGER</span>
      </div>
    </section>

    <section class="panel front">
      <div class="cover-art" role="img" aria-label="Foto: verrostetes, verlassenes Kreuzfahrtschiff mit Schornsteinen im Dunkeln"></div>
      <h1 class="title"><span>Was die</span><span class="second">Nacht behält</span></h1>
      <p class="front-author">MALTE BRÜNGER</p>
      <p class="genre">THRILLER</p>
    </section>
  </main>
</body>
</html>
```